Sports / Entertainment Media Co needs a biz card design

We are a media co / luxury lifestyle brand that targets professional athletes, entertainers and high net-worth fans. We are currently preparing for a relaunch and in need for new biz cards. I envision a black on black card with a pop of color on opposite side. Color Palette black, white, red etc. I want this card to exude sexiness and power. Very high stylized, hip and cool. I have attached the logo - I would like to see it all in black, but also open to other ideas. I will also upload a current card with all information needed on this new card. Furthermore I will add some samples of other cards I love. Thanks!!!
Updates

I provided suggestions, however I am open to all ideas!!   Be as creative as you can.  Think cutting-edge, sexy and powerful.  Take a look at the cards I uploaded to get a sense for what I like.  Thanks!!!

Industry/Entity Type

Entertainment

```html
<!DOCTYPE html>
<html lang="en">
<head>
<meta charset="utf-8">
<title>Stride business card</title>
<link href="https://fonts.googleapis.com/css2?family=Exo+2:wght@400;600&display=swap" rel="stylesheet">
<style>
  :root {
    --ink: #0d0d0d;
    --paper: #ffffff;
    --mist: #d2d2d2;
    --signal: #e3161b;
    --text-dark: #222222;
    --stage: #3a3a3c;
  }
  * { box-sizing: border-box; margin: 0; padding: 0; }
  html, body {
    width: 1200px; height: 974px; overflow: hidden;
    background: var(--stage);
    font-family: "Exo 2", sans-serif;
  }
  .canvas { position: relative; width: 1200px; height: 974px; }
  .card {
    position: absolute; top: 87px; width: 460px; height: 800px;
    background: var(--ink); overflow: hidden;
    box-shadow: 0 18px 40px rgba(0,0,0,.45);
  }
  .card--back { left: 100px; }
  .card--front { left: 640px; display: flex; flex-direction: column; }

  /* brand name placeholder */
  .brand {
    font-weight: 600; color: var(--ink); letter-spacing: 6px; line-height: 1;
    white-space: nowrap;
  }

  /* back side */
  .back__face {
    height: 690px; background: var(--paper);
    border-radius: 0 0 30px 30px;
    display: flex; align-items: center; justify-content: center;
  }
  .back__face .brand { font-size: 64px; }
  .back__web {
    height: 110px; display: flex; align-items: center; justify-content: center;
    color: var(--paper); font-size: 18px; letter-spacing: 1.5px;
  }

  /* front side */
  .front__logo {
    height: 190px; background: var(--paper);
    display: flex; align-items: center; justify-content: center;
  }
  .front__logo .brand { font-size: 50px; }
  .front__identity {
    height: 100px; color: var(--paper); text-align: center;
    display: flex; flex-direction: column; justify-content: center;
  }
  .identity__name { font-size: 30px; font-weight: 600; letter-spacing: 2px; }
  .identity__title { font-size: 17px; letter-spacing: 3px; margin-top: 2px; }
  .front__details { margin-left: 28px; display: flex; flex-direction: column; }
  .detail {
    display: flex; align-items: center; gap: 26px;
    padding-left: 46px; color: var(--text-dark); font-size: 19px; letter-spacing: 1px;
    background: var(--paper);
  }
  .detail--phone { height: 130px; }
  .detail--mail { height: 100px; background: var(--mist); }
  .detail--address { height: 130px; }
  .detail__icon { width: 40px; height: 40px; flex: none; }
  .detail__lines { line-height: 1.35; }
  .front__web {
    flex: 1; background: var(--signal); border-radius: 40px 0 0 0;
    display: flex; align-items: center; justify-content: center;
    color: var(--paper); font-size: 19px; letter-spacing: 1.5px;
  }
</style>
</head>
<body>
<main class="canvas">

  <section class="card card--back" aria-label="Card back">
    <div class="back__face">
      <span class="brand">STRIDE</span>
    </div>
    <div class="back__web">www.stridemedia.co</div>
  </section>

  <section class="card card--front" aria-label="Card front">
    <div class="front__logo">
      <span class="brand">STRIDE</span>
    </div>

    <div class="front__identity">
      <p class="identity__name">DANA REYES</p>
      <p class="identity__title">GENERAL MANAGER</p>
    </div>

    <div class="front__details">
      <div class="detail detail--phone">
        <svg class="detail__icon" viewBox="0 0 40 40" aria-hidden="true">
          <path d="M4 14c0-5 7-8 16-8s16 3 16 8v3h-8v-4c-2-1-5-1.5-8-1.5s-6 .5-8 1.5v4H4z" fill="#222"/>
          <path d="M10 20l4-5h12l4 5v12H10z" fill="#222"/>
          <circle cx="20" cy="25" r="3.5" fill="#fff"/>
        </svg>
        <div class="detail__lines">
          <p>020 555 0147</p>
          <p>020 555 0148</p>
        </div>
      </div>

      <div class="detail detail--mail">
        <svg class="detail__icon" viewBox="0 0 40 40" aria-hidden="true">
          <rect x="4" y="10" width="32" height="21" fill="#222"/>
          <path d="M5 11l15 12 15-12" fill="none" stroke="#d2d2d2" stroke-width="2"/>
        </svg>
        <div class="detail__lines"><p>dana@stridemedia.co</p></div>
      </div>

      <div class="detail detail--address">
        <svg class="detail__icon" viewBox="0 0 40 40" aria-hidden="true">
          <path d="M20 3a11 11 0 0 0-11 11c0 9 11 23 11 23s11-14 11-23A11 11 0 0 0 20 3z" fill="#222"/>
          <circle cx="20" cy="14" r="4.5" fill="#fff"/>
        </svg>
        <div class="detail__lines">
          <p>42 Harbor Lane</p>
          <p>Suite 5, West Block</p>
        </div>
      </div>
    </div>

    <div class="front__web">www.stridemedia.co</div>
  </section>

</main>
</body>
</html>
```